To design a brand identity that is simple and creative with 'Corvane' as the brand name, I like modern simple fonts like helvetica neue, I want to print both sides of the card, I am open to dark front and white back, but the design needs to transfer well to letter heads and email signatures, I am looking for sophisticated and elegant, but open minded about clever and off the wall, I do not do 'boring' Corvane Ventures is the mother company for a small group, specialising in Management & consulting, Software development and construction, we have a high level of integrity, we are transparent and accountable for what we do. my images are provided as a guide only, Im not expecting them to be just copied, Im looking for a creator and passionate thinker, who will put life into their work.

Target Market(s)

usually business minded people who are looking for something different in me, such as leadership, confidence and focus with thinking that is per haps a little outside the box..

Industry/Entity Type

Construction

Requirements
Must have
• clean, minmalistic
Nice to have
• custom logo
Should not have
• boring, traditional

```html
<!DOCTYPE html>
<html lang="en">
<head>
<meta charset="utf-8">
<title>Corvane Ventures — Business Card</title>
<link rel="stylesheet" href="https://fonts.googleapis.com/css2?family=Open+Sans:wght@400;700&display=swap">
<style>
  :root {
    --canvas: #e9e9ee;
    --ink-dark: #231f20;
    --brand-orange: #ef5a24;
    --paper: #ffffff;
    --tagline-grey: #6d6d6d;
    --strip-yellow: #f7b21b;
    --strip-red: #e2213a;
    --strip-purple: #8e3a7c;
    --strip-grey: #7b7b7b;
    --strip-teal: #1fa58e;
    --text-light: #ffffff;
  }
  * { box-sizing: border-box; margin: 0; padding: 0; }
  html, body {
    width: 1200px; height: 987px; overflow: hidden;
    background: var(--canvas);
    font-family: "Open Sans", Arial, sans-serif;
  }
  .canvas {
    width: 1200px; height: 987px;
    display: flex; flex-direction: column; align-items: center; justify-content: center; gap: 40px;
  }
  .card {
    position: relative; width: 760px; height: 434px;
    border-radius: 26px; overflow: hidden;
    box-shadow: 0 6px 18px rgba(0,0,0,.12);
  }

  .brand { display: flex; align-items: center; gap: 20px; }
  .brand__mark { width: 40px; height: 40px; background: var(--brand-orange); flex: none; }
  .brand__name {
    font-family: "Open Sans", Arial, sans-serif; font-weight: 400;
    font-size: 84px; line-height: 1; letter-spacing: 1px;
  }

  /* Front */
  .card--front { background: var(--ink-dark); }
  .card--front .brand { position: absolute; left: 70px; top: 86px; }
  .card--front .brand__name { color: var(--text-light); }

  .contact-band {
    position: absolute; left: 0; right: 0; top: 250px; height: 128px;
    background: var(--brand-orange); color: var(--text-light);
    display: flex; align-items: center; padding-left: 70px;
  }
  .person { text-align: right; padding-right: 22px; border-right: 1px solid rgba(255,255,255,.6); }
  .person__name { font-weight: 700; font-size: 24px; line-height: 1.2; }
  .person__title { font-size: 18px; line-height: 1.3; }
  .contact-list { list-style: none; padding-left: 22px; font-size: 17px; line-height: 1.55; }
  .contact-list li { display: flex; align-items: center; gap: 8px; }
  .contact-list svg { width: 16px; height: 16px; flex: none; }

  .services-strip {
    position: absolute; left: 0; right: 0; bottom: 0; height: 56px;
    background: linear-gradient(90deg, var(--strip-yellow) 0%, var(--brand-orange) 14%, var(--strip-red) 30%, var(--strip-purple) 55%, var(--strip-grey) 80%, var(--strip-teal) 100%);
    color: var(--text-light); font-weight: 700; font-size: 22px;
    display: flex; align-items: center; padding-left: 70px; letter-spacing: .3px;
  }

  /* Back */
  .card--back {
    background: var(--paper);
    display: flex; flex-direction: column; align-items: center; justify-content: center; gap: 18px;
  }
  .card--back .brand__name { color: var(--brand-orange); }
  .tagline {
    font-size: 22px; color: var(--tagline-grey); letter-spacing: 1px;
  }
</style>
</head>
<body>
<main class="canvas">
  <section class="card card--front" aria-label="Card front">
    <div class="brand">
      <span class="brand__mark"></span>
      <span class="brand__name">Corvane</span>
    </div>
    <div class="contact-band">
      <div class="person">
        <p class="person__name">Your Name</p>
        <p class="person__title">Title</p>
      </div>
      <ul class="contact-list">
        <li>
          <svg viewBox="0 0 16 16" aria-hidden="true"><circle cx="8" cy="8" r="7" fill="none" stroke="#fff" stroke-width="1.4"/><path d="M5.5 4.5l1.6 1.6-.9 1.2c.6 1.1 1.4 1.9 2.5 2.5l1.2-.9 1.6 1.6-1 1c-2.8-.4-5.6-3.2-6-6z" fill="#fff"/></svg>
          +61 0400 555 019
        </li>
        <li>
          <svg viewBox="0 0 16 16" aria-hidden="true"><rect x="1.5" y="3.5" width="13" height="9" rx="1" fill="#fff"/><path d="M1.5 4l6.5 5 6.5-5" fill="none" stroke="#ef5a24" stroke-width="1.3"/></svg>
          names@corvane.ventures
        </li>
        <li>Po Box 512 Perth 6000</li>
      </ul>
    </div>
    <div class="services-strip">Management • Software • Construction</div>
  </section>

  <section class="card card--back" aria-label="Card back">
    <div class="brand">
      <span class="brand__mark"></span>
      <span class="brand__name">Corvane</span>
    </div>
    <p class="tagline">building what comes next</p>
  </section>
</main>
</body>
</html>
```